Mental Health care Company in Washington DC

We are a new mental health care services provider in Washington DC. Please look at these sites.
https://brightwaterfamilysupport.com
https://www.quietharborinc.com
https://willowgate-dc.org/
https://www.tidepathdc.com
https://www.thelanternofdc.com

```html
<!DOCTYPE html>
<html lang="en">
<head>
<meta charset="utf-8">
<title>Lumen Ridge Services — Mental Health Care in Washington DC</title>
<link href="https://fonts.googleapis.com/css2?family=Poppins:ital,wght@0,400;0,500;0,600;0,700;0,800;1,400&display=swap" rel="stylesheet">
<style>
:root{
  --navy:#0d1f44;
  --navy-deep:#0a1a3a;
  --orange:#f5841f;
  --orange-soft:#f4a565;
  --teal:#a9dde0;
  --teal-dark:#7cc7cc;
  --gray-bg:#efefef;
  --text:#444a55;
  --muted:#8a9099;
  --white:#ffffff;
}
*{box-sizing:border-box;margin:0;padding:0}
html,body{width:1200px;height:4364px;overflow:hidden}
body{font-family:'Poppins',sans-serif;color:var(--text);background:var(--white);position:relative}
section,header,footer{position:relative;width:1200px;overflow:hidden}
.btn{position:absolute;display:flex;align-items:center;justify-content:center;font-weight:500;border-radius:22px;white-space:nowrap}
.btn-orange{background:var(--orange);color:var(--white)}
.btn-teal{background:var(--teal);color:var(--navy);border-radius:3px;font-size:13px;letter-spacing:.5px}
.section-title{position:absolute;left:0;width:1200px;text-align:center;font-size:31px;color:var(--navy);font-weight:400;letter-spacing:.5px}
.section-title b{font-weight:800}

/* header */
.site-header{height:85px;border-top:3px solid var(--navy);background:var(--white);box-shadow:0 2px 6px rgba(0,0,0,.05)}
.brand{position:absolute;left:141px;top:18px;text-align:center;width:190px}
.brand-name{font-size:28px;font-weight:500;color:var(--navy);line-height:1;letter-spacing:-.5px;white-space:nowrap}
.brand-sub{font-size:11px;letter-spacing:7px;color:var(--muted);margin-top:4px}
.main-nav{position:absolute;left:414px;top:32px;display:flex;gap:30px;font-size:13px;color:var(--navy);font-weight:500;white-space:nowrap}
.nav-cta{left:865px;top:22px;width:194px;height:38px;font-size:13px}

/* hero */
.hero{height:552px}
.hero-photo{position:absolute;inset:0;background:linear-gradient(90deg,#0d2a5a 0%,#284b78 28%,#8aa4c0 52%,#c9d6e0 72%,#e8ecef 100%)}
.hero h1{position:absolute;left:141px;top:128px;font-size:50px;line-height:56px;color:var(--white);font-weight:700;white-space:nowrap}
.hero h1 i{color:var(--teal);font-style:normal}
.hero p{position:absolute;left:141px;top:260px;font-size:15px;line-height:27px;color:var(--white)}
.hero-cta{left:141px;top:348px;width:140px;height:35px;font-size:13px}

/* about */
.about{height:648px}
.about-photo{position:absolute;left:141px;top:53px;width:460px;height:505px;border-radius:40px;background:radial-gradient(circle at 50% 50%,#b9c9cf 0%,#d8e2e4 45%,#f3f5f6 80%)}
.about h2{position:absolute;left:670px;top:122px;font-size:32px;font-weight:400;color:var(--navy);white-space:nowrap}
.about h2 b{font-weight:800}
.about .kicker{position:absolute;left:666px;top:162px;font-size:21px;color:#a7adb5;font-weight:500;letter-spacing:.5px}
.about .kicker::after{content:"";display:inline-block;width:72px;height:1px;background:#b8bec5;vertical-align:middle;margin-left:10px}
.about .copy{position:absolute;left:667px;top:202px;width:395px;font-size:13px;line-height:21.5px}
.about .copy p{margin-bottom:14px}
.about-more{left:667px;top:478px;width:127px;height:42px}

/* services */
.services{height:551px;background:var(--gray-bg)}
.services .section-title{top:85px}
.service-card{position:absolute;top:151px;width:284px;height:306px;background:var(--white);border-radius:8px;box-shadow:0 6px 18px rgba(0,0,0,.06);text-align:center}
.service-icon{display:block;margin:30px auto 0;width:86px;height:86px}
.service-card h3{font-size:17px;font-weight:600;color:var(--navy);margin-top:14px}
.service-card p{font-size:12.5px;line-height:21.5px;margin:11px 20px 0}

/* testimonials */
.testimonials{height:522px}
.testimonials .section-title{top:90px}
.avatar{position:absolute;border-radius:50%;background:radial-gradient(circle at 50% 40%,#c9b7a8 0%,#8e8a86 60%,#e7e7e7 100%)}
.stars{position:absolute;top:161px;left:0;width:1200px;text-align:center;color:var(--orange-soft);font-size:19px;letter-spacing:5px}
.quote{position:absolute;top:198px;left:320px;width:560px;text-align:center;font-style:italic;font-size:14px;line-height:24px}
.client-name{position:absolute;top:337px;left:0;width:1200px;text-align:center;font-size:16px;font-weight:600;color:var(--navy);letter-spacing:.5px}
.client-place{position:absolute;top:364px;left:0;width:1200px;text-align:center;font-size:13.5px}
.dots{position:absolute;top:397px;left:580px;display:flex;gap:10px}
.dots span{width:10px;height:10px;border-radius:50%;border:1px solid #9aa0a8}
.dots .on{background:var(--teal);border-color:var(--teal)}

/* why choose */
.why{height:712px;background:var(--gray-bg)}
.why .section-title{top:85px}
.why-ring{position:absolute;left:0;top:0}
.feature h3{font-size:17px;font-weight:600;color:var(--navy)}
.feature p{font-size:12.5px;line-height:22px;margin-top:6px}
.feature-left{position:absolute;left:105px;top:192px;width:258px;text-align:right}
.feature-right{position:absolute;left:832px;top:192px;width:260px}
.feature-bottom{position:absolute;left:669px;top:532px;width:245px}

/* contact */
.contact{height:557px}
.contact .section-title{top:88px}
.contact-intro{position:absolute;top:138px;left:370px;width:460px;text-align:center;font-size:13px;line-height:22px}
.field{position:absolute;height:40px;border:1px solid #d2d6da;border-radius:3px;background:var(--white);display:flex;align-items:center;font-size:12px;color:#555}
.field .ico{width:36px;height:100%;border-right:1px solid #e1e4e7;display:flex;align-items:center;justify-content:center;margin-right:11px}
.field-msg{align-items:flex-start;height:82px}
.field-msg .ico{height:100%;align-items:flex-start;padding-top:11px}
.field-msg span{padding-top:11px}
.submit{left:536px;top:424px;width:128px;height:40px;font-weight:600;font-size:12.5px}

/* CTA */
.cta{height:351px}
.cta-photo{position:absolute;inset:0;background:linear-gradient(180deg,#5d7e93 0%,#7f99a8 30%,#3f5b5d 52%,#6d8fa3 70%,#2f4c66 100%)}
.cta h2{position:absolute;top:75px;left:0;width:1200px;text-align:center;color:var(--white);font-size:27px;font-weight:400;letter-spacing:.5px}
.cta h2 b{font-weight:700}
.cta p{position:absolute;top:116px;left:0;width:1200px;text-align:center;color:var(--white);font-size:21px}
.cta-btn{left:497px;top:173px;width:205px;height:40px;border-radius:3px;font-size:12.5px;color:var(--navy);font-weight:600}

/* footer */
.site-footer{height:386px;background:var(--navy-deep);color:var(--white)}
.site-footer h4{position:absolute;top:60px;font-size:15px;font-weight:700;letter-spacing:.3px}
.site-footer h4::after{content:"";display:block;width:34px;height:2px;background:var(--orange);margin-top:8px}
.quick-links{position:absolute;left:143px;top:108px;list-style:none;font-size:13px;line-height:28px}
.quick-links li::before{content:"• "}
.contact-list{position:absolute;left:370px;top:108px;width:260px;font-size:12.5px;line-height:18px}
.contact-item{position:relative;padding-left:24px;margin-bottom:14px}
.contact-item svg{position:absolute;left:0;top:2px}
.contact-item b{display:block;font-weight:600}
.social{position:absolute;left:673px;top:110px;font-size:13px}
.social div{display:flex;align-items:center;gap:10px;height:41px}
.social span{width:28px;height:28px;border:1.5px solid var(--white);border-radius:50%;display:inline-block}
.footer-mark{position:absolute;left:858px;top:160px;width:220px;text-align:center;font-size:28px;font-weight:500;line-height:1.2;white-space:nowrap}
.footer-rule{position:absolute;left:141px;top:330px;width:918px;height:1px;background:rgba(255,255,255,.18)}
.copyright{position:absolute;top:350px;left:0;width:1200px;text-align:center;font-size:12.5px}
</style>
</head>
<body>

<header class="site-header">
  <div class="brand">
    <div class="brand-name">Lumen Ridge</div>
    <div class="brand-sub">SERVICES</div>
  </div>
  <nav class="main-nav">
    <span>Home</span><span>About Us ▾</span><span>Services ▾</span><span>Blog</span><span>FAQs</span><span>Contact</span>
  </nav>
  <div class="btn btn-orange nav-cta">Make an Appointment</div>
</header>

<section class="hero">
  <div class="hero-photo" role="img" aria-label="Smiling doctor in a white coat with a stethoscope talking with a patient in a bright clinic"></div>
  <h1>Empowering Minds<i>.</i><br>Restoring Lives<i>.</i></h1>
  <p>Compassionate, Client-Centered Mental Health Services<br>Tailored For Washington DC’s Diverse Communities.</p>
  <div class="btn btn-orange hero-cta">Get Started</div>
</section>

<section class="about">
  <div class="about-photo" role="img" aria-label="Woman in a standing yoga pose, framed in soft muted tones"></div>
  <h2>ABOUT <b>LUMEN RIDGE</b></h2>
  <div class="kicker">SERVICES</div>
  <div class="copy">
    <p>Lorem ipsum dolor sit amet, consectetuer adipiscing elit sed diam nonummy nibh euismod tincidunt ut laoet dolo magna aliquam erat volutpat.</p>
    <p>Ut wisi enim ad minim veniam, quis nostrud exer ullamcorper suscipit lobortis nisl ut aliquip ex ea commodo consequat. Duis autem vel eum iriure dolor in hendrerit in vulputate velit esse molestie consequat, vel illum dolore eu feugilla facilisis at vero eros et accumsan et iusto odio dignissim qui blandit praesent luptatum zzril delenit augue duis dolore te feugait nulla facilisi. Lorem ipsum dolor sit amet, consectetuer adipiscing elit, sed diam nonummy.</p>
  </div>
  <div class="btn btn-teal about-more">READ MORE</div>
</section>

<section class="services">
  <h2 class="section-title">OUR <b>SERVICES</b></h2>
  <div class="service-card" style="left:141px">
    <svg class="service-icon" viewBox="0 0 86 86"><circle cx="43" cy="43" r="41" fill="none" stroke="#a9dde0" stroke-dasharray="2 3"/><circle cx="43" cy="43" r="35" fill="#a9dde0"/><g fill="none" stroke="#0d1f44" stroke-width="2"><circle cx="43" cy="31" r="5"/><path d="M33 55h20M36 55l3-14h8l3 14M30 60h26"/></g></svg>
    <h3>Individual Therapy</h3>
    <p>Ut wisi enim ad minim v quis nostrud exerci taton ullamcorper spit lobortis nisl ut aliquip ex ea comghmodo consequat. Duis autem vel eum iriure dolor in hendrerit in vulputa.</p>
  </div>
  <div class="service-card" style="left:456px">
    <svg class="service-icon" viewBox="0 0 86 86"><circle cx="43" cy="43" r="41" fill="none" stroke="#f5841f" stroke-dasharray="2 3"/><circle cx="43" cy="43" r="35" fill="#f4a565"/><g fill="none" stroke="#0d1f44" stroke-width="2"><circle cx="43" cy="34" r="6"/><circle cx="30" cy="39" r="4.5"/><circle cx="56" cy="39" r="4.5"/><path d="M32 56c0-8 22-8 22 0zM21 54c0-6 10-7 12-4M65 54c0-6-10-7-12-4"/></g></svg>
    <h3>Group Therapy</h3>
    <p>Ut wisi enim ad minim v quis nostrud exerci taton ullamcorper spit lobortis nisl ut aliquip ex ea comghmodo consequat. Duis autem vel eum iriure dolor in hendrerit in vulputa.</p>
  </div>
  <div class="service-card" style="left:775px">
    <svg class="service-icon" viewBox="0 0 86 86"><circle cx="43" cy="43" r="41" fill="none" stroke="#a9dde0" stroke-dasharray="2 3"/><circle cx="43" cy="43" r="35" fill="#a9dde0"/><g fill="none" stroke="#0d1f44" stroke-width="2"><circle cx="43" cy="35" r="8"/><path d="M27 30v16l10 12M59 30v16L49 58"/></g></svg>
    <h3>Psychiatric Services</h3>
    <p>Ut wisi enim ad minim v quis nostrud exerci taton ullamcorper spit lobortis nisl ut aliquip ex ea comghmodo consequat. Duis autem vel eum iriure dolor in hendrerit in vulputa.</p>
  </div>
</section>

<section class="testimonials">
  <div class="avatar" style="left:229px;top:78px;width:98px;height:98px" role="img" aria-label="Portrait of a client in a suit"></div>
  <div class="avatar" style="left:122px;top:228px;width:68px;height:68px" role="img" aria-label="Portrait of a client with glasses"></div>
  <div class="avatar" style="left:250px;top:349px;width:80px;height:80px" role="img" aria-label="Portrait of a smiling client"></div>
  <div class="avatar" style="left:983px;top:103px;width:112px;height:112px" role="img" aria-label="Portrait of a bearded client"></div>
  <div class="avatar" style="left:895px;top:286px;width:102px;height:102px" role="img" aria-label="Portrait of a client with long hair"></div>
  <h2 class="section-title">WHAT OUR <b>CLIENTS SAY</b></h2>
  <div class="stars">★★★★★</div>
  <p class="quote">“Lorem ipsum dolor sit amet, consectetuer adipiscing elit, sed diam nonummy nibh euismod tincidunt ut laoreet dolore magna aliquam erat volutpat. Ut wisi enim ad minim veniam, quis nostrud exerci tation ullamcorper suscipit lobortis nisl ut aliquip ex ea commodo consequat. Duis autem vel eum iriure dolor in hendrerit in vulputate velit.”</p>
  <div class="client-name">DANA &amp; LEO K.</div>
  <div class="client-place">Austin, TX</div>
  <div class="dots"><span></span><span class="on"></span><span></span></div>
</section>

<section class="why">
  <h2 class="section-title">WHY <b>CHOOSE US</b></h2>
  <svg class="why-ring" width="1200" height="712" viewBox="0 0 1200 712">
    <circle cx="600" cy="366" r="203" fill="none" stroke="#a9dde0" stroke-width="2"/>
    <path d="M600 163 A203 203 0 0 1 750 500" fill="none" stroke="#f4a565" stroke-width="2"/>
    <circle cx="600" cy="366" r="190" fill="#ffffff"/>
    <circle cx="489" cy="184" r="5" fill="#fff" stroke="#a9dde0" stroke-width="1.5"/>
    <circle cx="790" cy="322" r="5" fill="#fff" stroke="#f4a565" stroke-width="1.5"/>
    <circle cx="517" cy="512" r="5" fill="#fff" stroke="#a9dde0" stroke-width="1.5"/>
    <circle cx="600" cy="366" r="90" fill="#f7fafa"/>
    <g>
      <path d="M384 253 A58 58 0 0 0 492 275" fill="none" stroke="#a9dde0" stroke-width="10"/>
      <circle cx="434" cy="245" r="50" fill="#fff" stroke="#eef2f3" stroke-width="2"/>
      <g fill="none" stroke="#0d1f44" stroke-width="2"><rect x="418" y="228" width="26" height="32" rx="2"/><path d="M424 238h14M424 246h10"/><circle cx="449" cy="254" r="8"/></g>
    </g>
    <g>
      <path d="M710 253 A58 58 0 0 0 818 275" fill="none" stroke="#a9dde0" stroke-width="10" transform="rotate(180 764 264)"/>
      <circle cx="764" cy="245" r="50" fill="#fff" stroke="#eef2f3" stroke-width="2"/>
      <g fill="none" stroke="#0d1f44" stroke-width="2"><circle cx="764" cy="236" r="9"/><path d="M746 266c0-14 36-14 36 0z"/></g>
    </g>
    <g>
      <path d="M540 523 A60 60 0 0 1 660 523" fill="none" stroke="#f4a565" stroke-width="10"/>
      <circle cx="600" cy="523" r="50" fill="#fff" stroke="#eef2f3" stroke-width="2"/>
      <g fill="none" stroke="#0d1f44" stroke-width="2"><circle cx="600" cy="523" r="20"/><circle cx="600" cy="518" r="5"/><path d="M590 532c3-7 17-7 20 0"/></g>
    </g>
  </svg>
  <div class="feature feature-left"><h3>Flexible Scheduling</h3><p>We offer evening and weekend appointments to accommodate your busy lifestyle.</p></div>
  <div class="feature feature-right"><h3>Experienced Therapists</h3><p>Our team consists of licensed professionals with years of experience in various mental health specialties.</p></div>
  <div class="feature feature-bottom"><h3>Personalized Approach</h3><p>We develop individualized treatment plans tailored to your unique needs and circumstances.</p></div>
</section>

<section class="contact">
  <h2 class="section-title">GET IN <b>TOUCH</b></h2>
  <p class="contact-intro">Lorem ipsum dolor sit amet, consectetuer adipiscing elit sed diam nonummy nibh euismod tincidunt.</p>
  <div class="field" style="left:303px;top:198px;width:289px"><div class="ico"><svg width="12" height="12" viewBox="0 0 12 12"><circle cx="6" cy="4" r="3" fill="#f4a565"/><path d="M1 12c0-5 10-5 10 0z" fill="#f4a565"/></svg></div><span>First Name*</span></div>
  <div class="field" style="left:608px;top:198px;width:289px"><div class="ico"><svg width="12" height="12" viewBox="0 0 12 12"><circle cx="6" cy="4" r="3" fill="#f4a565"/><path d="M1 12c0-5 10-5 10 0z" fill="#f4a565"/></svg></div><span>Last Name*</span></div>
  <div class="field" style="left:303px;top:253px;width:289px"><div class="ico"><svg width="12" height="12" viewBox="0 0 12 12"><path d="M2 1l3 0 1 3-2 1c1 2 2 3 3 3l1-2 3 1 0 3c-6 1-10-3-9-9z" fill="#f4a565"/></svg></div><span>Your Phone*</span></div>
  <div class="field" style="left:608px;top:253px;width:289px"><div class="ico"><svg width="12" height="10" viewBox="0 0 12 10"><rect width="12" height="10" rx="1" fill="#f4a565"/><path d="M0 1l6 4 6-4" stroke="#fff" fill="none"/></svg></div><span>Your Email*</span></div>
  <div class="field field-msg" style="left:303px;top:308px;width:594px"><div class="ico"><svg width="13" height="11" viewBox="0 0 13 11"><ellipse cx="6" cy="4.5" rx="6" ry="4.5" fill="#f4a565"/><path d="M2 8l-1 3 4-2z" fill="#f4a565"/></svg></div><span>Your Message</span></div>
  <div class="btn btn-teal submit">SUBMIT NOW</div>
</section>

<section class="cta">
  <div class="cta-photo" role="img" aria-label="Person meditating on a wooden dock beside a calm mountain lake"></div>
  <h2>READY TO START YOUR <b>JOURNEY TO WELLNESS?</b></h2>
  <p>Schedule a consultation with one of our experienced therapists today.</p>
  <div class="btn btn-orange cta-btn">SCHEDULE CONSULTATION</div>
</section>

<footer class="site-footer">
  <h4 style="left:143px">QUICK LINKS</h4>
  <ul class="quick-links"><li>Home</li><li>About Us</li><li>Services</li><li>Our Team</li><li>Contact Us</li></ul>
  <h4 style="left:370px">CONTACT DETAILS</h4>
  <div class="contact-list">
    <div class="contact-item"><svg width="12" height="15" viewBox="0 0 12 15"><path d="M6 0a6 6 0 0 1 6 6c0 4-6 9-6 9S0 10 0 6a6 6 0 0 1 6-6z" fill="#fff"/><circle cx="6" cy="6" r="2" fill="#0a1a3a"/></svg><b>ADDRESS</b>480 Larkspur Row, Suite 12<br>Fernvale, DC 20099</div>
    <div class="contact-item"><svg width="13" height="13" viewBox="0 0 12 12"><path d="M2 1l3 0 1 3-2 1c1 2 2 3 3 3l1-2 3 1 0 3c-6 1-10-3-9-9z" fill="#fff"/></svg><b>PHONE</b>202 555 0148</div>
    <div class="contact-item"><svg width="13" height="10" viewBox="0 0 12 10"><rect width="12" height="10" rx="1" fill="#fff"/><path d="M0 1l6 4 6-4" stroke="#0a1a3a" fill="none"/></svg><b>EMAIL</b>info@lumenridgehealth.com</div>
  </div>
  <h4 style="left:673px">FOLLOW US</h4>
  <div class="social">
    <div><span></span>Community Page</div>
    <div><span></span>Video Channel</div>
    <div><span></span>Photo Journal</div>
    <div><span></span>Daily Updates</div>
  </div>
  <div class="footer-mark">Lumen Ridge</div>
  <div class="footer-rule"></div>
  <div class="copyright">© 2025 Lumen Ridge Services. All Rights Reserved.</div>
</footer>

</body>
</html>
```